Bramblewood Card Company Business Cards

We are a trading card store with Glimmorax, sports and other TCG cards, we need a business card design that encompasses a clean cut, modern style with a retro flare. website is bramblewoodcardco.com for reference. Can utilize a comic book era feel or a more modern outdoor feel to utilize the "Pacific Northwest" elements of tress, mountains, etc.

Industry/Entity Type

Trading cards and collectibles

Contact Information for Business Card

business name, email address, phone number, name, owner job title

Font styles to use
Sans Serif

```html
<!DOCTYPE html>
<html lang="en">
<head>
<meta charset="utf-8">
<title>Bramblewood Card Company – Business Cards</title>
<link href="https://fonts.googleapis.com/css2?family=Montserrat:wght@400;500;700;800&display=swap" rel="stylesheet">
<style>
  :root {
    --stage: #2b2b2d;
    --card: #1d1d1f;
    --cyan: #1fc0e0;
    --white: #f2f2f2;
    --rule: #4a4a4c;
  }
  * { margin: 0; padding: 0; box-sizing: border-box; }
  html, body { width: 1200px; height: 801px; overflow: hidden; }
  body {
    background: var(--stage);
    font-family: "Montserrat", sans-serif;
    position: relative;
  }
  .card {
    position: absolute;
    top: 252px;
    width: 520px;
    height: 297px;
    border-radius: 18px;
    background: var(--card);
    overflow: hidden;
    box-shadow: 0 14px 30px rgba(0,0,0,.45);
  }
  .card--front { left: 60px; }
  .card--back { left: 620px; }

  /* front */
  .brand {
    position: absolute;
    left: 42px; top: 48px;
    display: flex; align-items: center; gap: 12px;
  }
  .brand__mark { width: 18px; height: 18px; background: var(--cyan); flex: none; }
  .brand__name {
    font-weight: 800; font-size: 19px; letter-spacing: .06em;
    text-transform: uppercase; color: var(--white); line-height: 1.2;
    width: 230px;
  }
  .person {
    position: absolute; left: 42px; top: 150px;
    width: 210px;
  }
  .person__name {
    font-weight: 700; font-size: 27px; color: var(--cyan);
    letter-spacing: .02em; text-transform: uppercase; white-space: nowrap;
  }
  .person__title {
    font-weight: 400; font-size: 15px; color: var(--white); margin-top: 2px;
  }
  .divider {
    position: absolute; left: 262px; top: 140px;
    width: 1px; height: 62px; background: var(--rule);
  }
  .contacts {
    position: absolute; left: 280px; top: 128px;
    list-style: none;
  }
  .contacts li {
    display: flex; align-items: center; gap: 8px;
    font-size: 12.5px; color: var(--white); height: 24px; white-space: nowrap;
  }
  .contacts svg { width: 12px; height: 12px; flex: none; }
  .contacts .accent { color: var(--cyan); }
  .address-band {
    position: absolute; left: 0; right: 0; top: 230px; height: 38px;
    background: var(--cyan);
    display: flex; align-items: center; padding-left: 42px;
    font-size: 14px; color: var(--white); letter-spacing: .01em; white-space: nowrap;
  }

  /* back */
  .pattern-field {
    position: absolute; inset: 0;
    background: linear-gradient(135deg, #1a1a1b 0%, #2c2c2e 55%, #4a4a4c 100%);
  }
  .back-brand {
    position: absolute; right: 56px; bottom: 62px;
    display: flex; align-items: center; gap: 8px;
  }
  .back-brand__mark { width: 12px; height: 12px; background: var(--cyan); }
  .back-brand__name {
    font-weight: 800; font-size: 12px; letter-spacing: .06em;
    text-transform: uppercase; color: var(--white);
  }
</style>
</head>
<body>

<section class="card card--front" aria-label="Business card front">
  <div class="brand">
    <span class="brand__mark"></span>
    <span class="brand__name">Bramblewood Card Company</span>
  </div>

  <div class="person">
    <p class="person__name">Dorian Hale</p>
    <p class="person__title">CEO/Founder</p>
  </div>

  <span class="divider"></span>

  <ul class="contacts">
    <li>
      <svg viewBox="0 0 12 12" aria-hidden="true"><path fill="#1fc0e0" d="M2.5 1h2l1 2.6-1.3 1a6 6 0 0 0 2.9 2.9l1-1.3L11 7.5v2a1.4 1.4 0 0 1-1.5 1.4A9 9 0 0 1 1 2.5 1.4 1.4 0 0 1 2.5 1z"/></svg>
      (555) 318 2046
    </li>
    <li>
      <svg viewBox="0 0 12 12" aria-hidden="true"><rect x="0.5" y="2" width="11" height="8" rx="1" fill="#1fc0e0"/><path d="M1 2.5 6 6.5l5-4" fill="none" stroke="#1d1d1f" stroke-width="1"/></svg>
      info@bramblewoodcardco.com
    </li>
    <li>
      <svg viewBox="0 0 12 12" aria-hidden="true"><g fill="none" stroke="#1fc0e0" stroke-width="1"><circle cx="6" cy="6" r="5"/><ellipse cx="6" cy="6" rx="2.2" ry="5"/><path d="M1 6h10M2 3.3h8M2 8.7h8"/></g></svg>
      <span>www.<span class="accent">bramblewoodcardco</span>.com</span>
    </li>
  </ul>

  <div class="address-band">P.O. Box 3178 Cedar Lane Ridgefield WA 9861</div>
</section>

<section class="card card--back" aria-label="Business card back">
  <div class="pattern-field" role="img" aria-label="Repeating pattern of the company badge in dark and grey tones"></div>
  <div class="back-brand">
    <span class="back-brand__mark"></span>
    <span class="back-brand__name">Bramblewood Card Company</span>
  </div>
</section>

</body>
</html>
```